Velvet Harbor Snout Sticks - our own unique product line of cotton swabs

We have something now that we are not too happy with. Looking to create a label for a line of cotton swabs that we have created and designed to clean your nose from mucus and boogers. The logo that i have so far for the packaging is the white background with the black silhouette nose (attached). We need something that can do well in the retail/consumer market. Our website address (even though it is not live yet) should be listed somewhere on the label....
www.VelvetHarborGoods.example ( we sell pillows, but we have other product lines)
We would also like to see a brief description on how to correctly use the nose pick on the back side of the label. The description on how to use should read " insert cotton nose pick into nostril and give it a few counter clock wise twirls or till you feel mucus/debris latch onto the cotton. You may need to repeat the process and use more than one nose pick to achieve desired result."
As well as a warning mentioning : "Never insert plastic end of nose pick into any part of your body. Be careful and use with caution."
Also for you to know, the cotton is made from 100% natural cotton, the cotton head itself is thick and highly absorbent making it a pleasure to use. There are 50 nose picks per pack.
We're fine with keeping it simple and not making the packaging too busy, however we're open to your ideas and designs! I have given you the most important information relevant to the project. If there are any questions or something is not clear enough please kindly message me.

Requirements
Must have
• professional looking
clean looking
not busy
Should not have
• words clumping together making it appear as too much text in one area
too much text clumped together on the design

```html
<!DOCTYPE html>
<html lang="en">
<head>
<meta charset="utf-8">
<title>Velvet Harbor Snout Sticks – Cotton Swabs Label</title>
<link rel="stylesheet" href="https://fonts.googleapis.com/css2?family=Ubuntu+Condensed&family=Open+Sans:wght@400;600&family=Archivo+Black&family=Montserrat:ital,wght@1,800&display=swap">
<style>
  :root {
    --backdrop: #e6e6e6;
    --label: #ffffff;
    --ink: #222222;
    --ink-soft: #3a3a3a;
    --orange: #e0532a;
    --navy: #0b2a45;
    --teal: #1b8a86;
  }
  * { margin: 0; padding: 0; box-sizing: border-box; }
  html, body {
    width: 1200px; height: 1064px; overflow: hidden;
    background: var(--backdrop);
  }
  .label {
    position: absolute;
    left: 100px; top: 152px;
    width: 1000px; height: 760px;
    background: var(--label);
    overflow: hidden;
    box-shadow: 0 2px 10px rgba(0,0,0,0.08);
  }
  .accent-panel {
    position: absolute;
    right: 0; top: 0;
    width: 300px; height: 100%;
    background: linear-gradient(160deg, var(--navy) 0%, var(--teal) 100%);
  }
  .brand {
    position: absolute;
    left: 130px; top: 130px;
    width: 460px;
    text-align: center;
  }
  .brand-name {
    display: flex; align-items: center; justify-content: center; gap: 16px;
    font-family: "Ubuntu Condensed", sans-serif;
    font-size: 76px; line-height: 1;
    white-space: nowrap;
    color: var(--ink);
  }
  .brand-dot {
    flex: none;
    width: 18px; height: 18px; border-radius: 50%;
    background: var(--ink);
  }
  .brand-rule {
    margin: 22px auto 0;
    width: 340px; height: 3px;
    background: var(--ink);
  }
  .brand-line {
    margin-top: 22px;
    font-family: "Open Sans", sans-serif;
    font-size: 24px; letter-spacing: 6px;
    color: var(--ink-soft);
  }
  .product {
    position: absolute;
    left: 110px; top: 400px;
    font-family: "Archivo Black", sans-serif;
    font-size: 78px; line-height: 0.95;
    font-weight: 400;
    color: var(--orange);
  }
  .product span { display: block; }
  .web-pill {
    position: absolute;
    left: 190px; top: 684px;
    width: 460px; height: 38px;
    border-radius: 19px;
    background: var(--orange);
    display: flex; align-items: center; justify-content: center;
    font-family: "Montserrat", sans-serif;
    font-style: italic; font-weight: 800;
    font-size: 17px; color: #ffffff;
    letter-spacing: 0.5px;
    white-space: nowrap;
  }
</style>
</head>
<body>
  <main class="label">
    <div class="accent-panel" role="img" aria-label="Decorative flowing bands in navy, teal and gold"></div>

    <header class="brand">
      <div class="brand-name"><span class="brand-dot"></span>Velvet Harbor</div>
      <div class="brand-rule"></div>
      <div class="brand-line">Snout Sticks</div>
    </header>

    <h1 class="product">
      <span>COTTON</span>
      <span>SWABS</span>
    </h1>

    <div class="web-pill">www.VelvetHarborGoods.example</div>
  </main>
</body>
</html>
```